Real Estate Brokerage Stationery Designs

I am looking to have presentation folders with business card slots on both sides along with pockets on both sides. I've attached logos, website colors along with current business card designs.

I am looking for envelope designs both big and small. Possibly new business card designs, notepad templates for big and small notepads. Letterhead designs. Pop socket designs. Realtors name badge designs.

www.brightholdrealty.example

```html
<!DOCTYPE html>
<html lang="en">
<head>
<meta charset="utf-8">
<title>Brighthold Realty – Presentation Folder Interior</title>
<link rel="stylesheet" href="https://fonts.googleapis.com/css2?family=Jost:wght@400;500&family=Roboto:wght@400;700&display=swap">
<style>
  :root {
    --stage: #a7a7a7;
    --folder-blue: #0a5aa3;
    --pocket-blue: #0b5ca7;
    --pocket-shade: #084a87;
    --paper: #f2f2f2;
    --photo-mid: #cfd0d1;
    --faint-blue: #7d97b3;
    --card-white: #ffffff;
    --card-ink: #1d1d1d;
  }
  html, body {
    margin: 0;
    width: 1200px;
    height: 1200px;
    overflow: hidden;
    background: var(--stage);
  }
  .folder-spread { display: block; width: 1200px; height: 1200px; }
  .faint-headline { font-family: "Jost", sans-serif; font-weight: 500; fill: var(--faint-blue); opacity: .45; letter-spacing: 2px; }
  .faint-sub { font-family: "Jost", sans-serif; font-weight: 400; fill: var(--faint-blue); opacity: .45; letter-spacing: 1.5px; }
  .faint-body { font-family: "Jost", sans-serif; font-size: 12.5px; fill: var(--faint-blue); opacity: .45; }
  .pocket-contact { font-family: "Jost", sans-serif; fill: var(--pocket-shade); opacity: .55; }
  .card-brand { font-family: "Roboto", sans-serif; font-weight: 700; font-size: 11px; fill: var(--folder-blue); }
  .card-name { font-family: "Roboto", sans-serif; font-weight: 700; font-size: 10.5px; fill: var(--card-white); }
  .card-title { font-family: "Roboto", sans-serif; font-size: 5.5px; fill: var(--card-white); }
  .card-line { font-family: "Roboto", sans-serif; font-size: 5.6px; fill: var(--card-ink); }
</style>
</head>
<body>
<svg class="folder-spread" viewBox="0 0 1200 1200" xmlns="http://www.w3.org/2000/svg">
  <defs>
    <linearGradient id="house-photo-tone" x1="0" y1="0" x2="0" y2="1">
      <stop offset="0" stop-color="#f4f4f4"/>
      <stop offset=".45" stop-color="var(--photo-mid)"/>
      <stop offset="1" stop-color="#dcdcdc"/>
    </linearGradient>
    <linearGradient id="agent-photo-tone" x1="0" y1="0" x2="0" y2="1">
      <stop offset="0" stop-color="#e6e6e6"/>
      <stop offset="1" stop-color="#2a2d33"/>
    </linearGradient>

    <g id="realtor-card">
      <rect width="250" height="143" fill="var(--card-white)"/>
      <rect class="agent-photo" x="165" y="0" width="85" height="143" fill="url(#agent-photo-tone)"
            role="img" aria-label="Portrait photo of the realtor in a dark suit"/>
      <rect x="8" y="30" width="10" height="10" fill="var(--folder-blue)"/>
      <text class="card-brand" x="22" y="39">Brighthold Realty</text>
      <rect x="0" y="58" width="165" height="24" fill="var(--folder-blue)"/>
      <rect x="128" y="48" width="9" height="8" fill="var(--folder-blue)"/>
      <rect x="140" y="48" width="18" height="8" fill="var(--folder-blue)"/>
      <text class="card-name" x="8" y="71">MARCUS BELLAMY</text>
      <text class="card-title" x="8" y="79">REALTOR®</text>
      <text class="card-line" x="12" y="94">742 Harbor Point Dr,</text>
      <text class="card-line" x="12" y="101">Suite 110, Lakeview FL 33010</text>
      <g fill="var(--folder-blue)">
        <circle cx="15" cy="108" r="2"/><text class="card-line" x="20" y="110">555-201-4478</text>
        <circle cx="15" cy="115" r="2"/><text class="card-line" x="20" y="117">555-203-1190</text>
        <circle cx="15" cy="122" r="2"/><text class="card-line" x="20" y="124">555-207-3362</text>
        <circle cx="15" cy="129" r="2"/><text class="card-line" x="20" y="131">marcus@brightholdrealty.example</text>
        <circle cx="15" cy="136" r="2"/><text class="card-line" x="20" y="138">www.brightholdrealty.example</text>
      </g>
    </g>
  </defs>

  <!-- folder panels -->
  <rect class="panel-left" x="80" y="250" width="520" height="700" fill="var(--paper)"/>
  <rect class="panel-right" x="600" y="250" width="520" height="700" fill="var(--paper)"/>

  <!-- background house image area -->
  <rect class="house-photo" x="80" y="330" width="1040" height="430" fill="url(#house-photo-tone)" opacity=".75"
        role="img" aria-label="Faded black-and-white photograph of a large two-storey suburban house spanning both panels"/>
  <line class="spine" x1="600" y1="250" x2="600" y2="950" stroke="#d4d4d4" stroke-width="1"/>

  <!-- right panel lower band -->
  <rect class="band-right" x="600" y="680" width="520" height="270" fill="var(--folder-blue)"/>

  <!-- left panel faint copy -->
  <g class="intro-copy">
    <text class="faint-headline" x="125" y="420" font-size="34">LOCAL, TRUSTED REALTY</text>
    <text class="faint-sub" x="160" y="450" font-size="18">DEDICATED TO CLIENT SERVICE</text>
    <text class="faint-body" x="125" y="492">Brighthold Realty is a locally owned brokerage serving home buyers and</text>
    <text class="faint-body" x="125" y="510">sellers. Our commitment is to be your one point of contact for every</text>
    <text class="faint-body" x="125" y="528">residential or commercial move. We believe in outstanding client service</text>
    <text class="faint-body" x="125" y="546">and excellence in every transaction.</text>
    <text class="faint-body" x="125" y="572">Keeping to the HIGHEST standards of integrity. With hard work and care</text>
    <text class="faint-body" x="125" y="590">being an essential part of our core values, we've built a culture of respect,</text>
    <text class="faint-body" x="125" y="608">honesty and transparency in every part of our business.</text>
    <text class="faint-body" x="125" y="634">Buying or selling a home is one of the biggest decisions you will make.</text>
    <text class="faint-body" x="125" y="652">Our goal is to guide you home with trust, one closing at a time.</text>
  </g>

  <!-- left pocket -->
  <path class="pocket-left" d="M80,762 H540 Q566,762 572,786 L598,950 H80 Z" fill="var(--pocket-blue)"/>
  <path d="M540,762 Q566,762 572,786 L598,950" fill="none" stroke="var(--pocket-shade)" stroke-width="2" opacity=".5"/>
  <g class="contact-block">
    <text class="pocket-contact" x="112" y="822" font-size="20" font-weight="500" letter-spacing="2">CONTACT US</text>
    <g class="contact-row">
      <circle cx="120" cy="852" r="8" fill="none" stroke="var(--pocket-shade)" stroke-width="2" opacity=".55"/>
      <path d="M116,848 l3,0 l1,3 l-2,1 q2,3 4,4 l1,-2 l3,1 l0,3 q-10,0 -10,-10z" fill="var(--pocket-shade)" opacity=".55"/>
      <text class="pocket-contact" x="136" y="857" font-size="14">555-014-HOME</text>
    </g>
    <g class="contact-row">
      <circle cx="120" cy="882" r="8" fill="none" stroke="var(--pocket-shade)" stroke-width="2" opacity=".55"/>
      <rect x="115" y="879" width="10" height="7" fill="none" stroke="var(--pocket-shade)" stroke-width="1.5" opacity=".55"/>
      <text class="pocket-contact" x="136" y="887" font-size="13">info@brightholdrealty.example</text>
    </g>
    <g class="contact-row">
      <circle cx="120" cy="912" r="8" fill="none" stroke="var(--pocket-shade)" stroke-width="2" opacity=".55"/>
      <circle cx="120" cy="912" r="4" fill="none" stroke="var(--pocket-shade)" stroke-width="1.5" opacity=".55"/>
      <text class="pocket-contact" x="136" y="917" font-size="13">www.brightholdrealty.example</text>
    </g>
  </g>

  <!-- left business card slot -->
  <use class="business-card card-left" href="#realtor-card" transform="translate(335,790) scale(0.88)"/>
  <line class="card-slit" x1="324" y1="807" x2="350" y2="781" stroke="#ffffff" stroke-width="2.5"/>
  <line class="card-slit" x1="539" y1="924" x2="565" y2="898" stroke="#ffffff" stroke-width="2.5"/>

  <!-- right pocket -->
  <path class="pocket-right" d="M602,950 L628,742 Q632,720 656,720 H1120 V950 Z" fill="var(--pocket-blue)"/>
  <path d="M602,950 L628,742 Q632,720 656,720 H1120" fill="none" stroke="var(--pocket-shade)" stroke-width="2" opacity=".5"/>

  <!-- right business card slot -->
  <use class="business-card card-right" href="#realtor-card" transform="translate(855,775) scale(0.88)"/>
  <line class="card-slit" x1="844" y1="792" x2="870" y2="766" stroke="#ffffff" stroke-width="2.5"/>
  <line class="card-slit" x1="1059" y1="909" x2="1085" y2="883" stroke="#ffffff" stroke-width="2.5"/>
</svg>
</body>
</html>
```